Web design for consulting advisory business company

We need a web for our business consulting company. The web should transmit simplicity, innovation, trust, and solid knowledge of what we do. Inspirational webs to take a look are: https://brindlemoor.com/ and http://tavunexa.com.br. Use blue colors.

Target Market(s)

Private companies

Industry/Entity Type

Management Consulting

Number of Pages Required

5+ page

Font styles to use
Serif
Sans Serif

Colors
3176b5
3276b5
85abd2
85cae6
33a6d7
0592cd
ffffff
1b1b1b
474747

Requirements
Must have
• - use of blue
• - images
• - same version in different languages (portugueses and spanish)
Nice to have
• - white as background

```html
<!DOCTYPE html>
<html lang="pt">
<head>
<meta charset="utf-8">
<title>Cadence Partners</title>
<link href="https://fonts.googleapis.com/css2?family=Lato:wght@400;700;900&display=swap" rel="stylesheet">
<style>
:root{
  --blue:#3176b5;
  --blue-soft:#85abd2;
  --sky:#33a6d7;
  --ocean:#0592cd;
  --white:#ffffff;
  --ink:#1b1b1b;
  --text:#474747;
  --panel:#eeeeee;
  --team:#6e98ca;
}
*{box-sizing:border-box;margin:0;padding:0}
html,body{width:1200px;height:4627px;overflow:hidden}
body{font-family:'Lato',sans-serif;color:var(--text);background:var(--white)}
section{position:relative;width:1200px;overflow:hidden}
h2{font-weight:700;font-size:44px;text-align:center;color:var(--ink)}
p{font-size:15px;line-height:1.75}
.btn{display:block;margin:0 auto;width:206px;height:50px;border:2px solid var(--blue);color:var(--blue);font-weight:700;font-size:18px;text-align:center;line-height:46px}
.btn.light{border-color:var(--white);color:var(--white)}

/* hero */
.hero{height:694px;background:radial-gradient(circle at 70% 40%,#8a6e55 0%,#4c4844 35%,#2c3440 75%,#1e2733 100%)}
.hero .photo{position:absolute;inset:0}
.hero .shade{position:absolute;inset:0;background:linear-gradient(rgba(0,0,0,.35),rgba(0,0,0,.15) 40%,rgba(0,0,0,.35))}
.nav{position:absolute;top:38px;left:77px;right:77px;display:flex;align-items:center;color:var(--white)}
.brand{display:flex;align-items:center;gap:10px;font-weight:900;font-size:28px;letter-spacing:.5px}
.brand i{display:block;width:36px;height:36px;border:3px solid var(--white)}
.nav ul{list-style:none;display:flex;gap:26px;margin-left:auto;font-size:15px;font-weight:700}
.nav .lang{margin-left:60px;font-size:14px;font-weight:700}
.hero h1{position:absolute;top:272px;width:100%;text-align:center;color:var(--white);font-weight:900;font-size:66px;line-height:1;text-shadow:0 2px 6px rgba(0,0,0,.4)}
.hero .tag{position:absolute;top:404px;width:100%;text-align:center;color:var(--white);font-weight:700;font-size:28px}
.dots{display:flex;gap:9px;justify-content:center}
.dots b{width:10px;height:10px;border-radius:50%;background:var(--white);opacity:.6}
.dots b:first-child{opacity:1}
.hero .dots{position:absolute;top:642px;width:100%}

/* principles */
.principles{height:386px;padding-top:58px}
.principles p{width:1050px;margin:30px auto 38px;text-align:center}

/* expertise */
.expertise{height:910px;background:linear-gradient(180deg,#10202f 0%,#1c2d3c 30%,#31414e 60%,#26313b 100%)}
.expertise h2{color:var(--white);margin-top:60px}
.expertise > p{width:1060px;margin:22px auto 0;text-align:center;color:var(--white);font-size:15px}
.panel{position:absolute;left:77px;width:1046px;height:292px;background:var(--panel)}
.panel h3{text-align:center;color:var(--blue);font-size:34px;font-weight:700;margin-top:28px}
.cards{display:flex;gap:17px;justify-content:center;margin-top:20px}
.card{width:176px;height:156px;background:var(--white);box-shadow:0 1px 4px rgba(0,0,0,.15);text-align:center;padding-top:30px;color:var(--ink);font-weight:700;font-size:16px;line-height:1.3}
.card svg{display:block;margin:0 auto 12px;width:38px;height:38px;fill:var(--blue)}
.arrow{position:absolute;top:160px;font-size:26px;color:var(--ink);font-weight:700}
.arrow.l{left:12px}.arrow.r{right:12px}

/* cases */
.cases{height:648px;background:linear-gradient(120deg,var(--blue) 0%,var(--ocean) 100%);color:var(--white)}
.cases h2{color:var(--white);margin-top:52px}
.cases > p{text-align:center;margin-top:18px}
.case-photo{position:absolute;left:160px;top:180px;width:334px;height:398px;background:linear-gradient(135deg,#d8dde3,#8b95a1 55%,#4d5661)}
.case-list{position:absolute;left:525px;top:175px;width:510px;list-style:none}
.case-list li{position:relative;padding-left:34px;font-size:14.5px;line-height:1.75;margin-bottom:18px}
.case-list svg{position:absolute;left:0;top:4px;width:18px;height:18px}
.cases .btn{position:absolute;left:525px;top:510px}

/* ecosystem */
.ecosystem{height:432px;padding-top:50px}
.ecosystem > p{width:1040px;margin:20px auto 0;text-align:center}
.partners{display:flex;justify-content:center;gap:20px;margin-top:28px}
.partner{width:300px;text-align:center}
.partner h3{color:var(--blue);font-size:34px;font-weight:700}
.partner p{margin-top:6px;color:var(--text)}
.ecosystem .dots{margin-top:30px}
.ecosystem .dots b{background:var(--blue)}

/* team */
.team{height:533px;background:var(--team)}
.team h2{color:var(--white);margin-top:40px}
.members{display:flex;justify-content:center;gap:150px;margin-top:46px}
.member{width:290px;text-align:center;color:var(--white)}
.member .portrait{width:173px;height:185px;margin:0 auto;border:4px solid var(--white);background:linear-gradient(160deg,#c9ced4,#7c8591)}
.member h3{font-size:28px;font-weight:700;margin-top:18px;white-space:nowrap}
.member p{font-size:14.5px;line-height:1.6;margin-top:8px}

/* contact */
.contact{height:886px;padding-top:56px}
.contact .lead{text-align:center;color:var(--blue);font-weight:700;font-size:24px;margin-top:16px}
.contact .intro{width:980px;margin:12px auto 0;text-align:center}
.contact .intro a{color:var(--blue);text-decoration:none}
.form{width:690px;margin:30px auto 0;display:grid;grid-template-columns:1fr 1fr;gap:18px 24px}
.field{height:50px;border:1px solid #bdbdbd;font-size:13px;padding:10px 12px;color:var(--text)}
.field.msg{grid-column:1/3;height:110px}
.submit{display:block;width:175px;height:54px;margin:28px auto 0;background:var(--sky);color:var(--white);font-weight:700;font-size:20px;text-align:center;line-height:54px}
.offices{display:flex;justify-content:center;gap:30px;margin-top:70px}
.office{width:330px;height:178px;background:var(--panel);text-align:center;padding-top:26px}
.office h3{color:var(--blue);font-size:25px;font-weight:700}
.office p{font-size:14.5px;line-height:1.55;margin-top:10px}

/* footer */
.footer{height:138px;background:var(--ink);color:var(--white)}
.footer ul{position:absolute;left:77px;top:44px;list-style:none;display:flex;gap:22px;font-weight:700;font-size:16px}
.footer small{position:absolute;left:77px;top:80px;font-size:12px;color:#aaa}
.social{position:absolute;right:77px;top:44px;display:flex;gap:14px}
.social i{width:22px;height:22px;border-radius:50%;background:var(--white)}
</style>
</head>
<body>

<section class="hero">
  <div class="photo" role="img" aria-label="Consultores reunidos em torno de uma mesa de escritório"></div>
  <div class="shade"></div>
  <nav class="nav">
    <div class="brand"><i></i>CADENCE PARTNERS</div>
    <ul><li>Princípios</li><li>Expertise</li><li>Cases</li><li>Ecosistema</li><li>Equipe Sênior</li><li>Contato</li></ul>
    <div class="lang">PT | ES</div>
  </nav>
  <h1>WELCOME TO<br>CADENCE PARTNERS</h1>
  <div class="tag">We are a business consulting advisory company..</div>
  <div class="dots"><b></b><b></b><b></b></div>
</section>

<section class="principles">
  <h2>Princípios</h2>
  <p>Adaptamos a equipe e os esforços para o problema, combinando recursos sêniores e especialistas do setor com fortes recursos analíticos para fornecer soluções sustentáveis. Ouvimos atentamente os nossos clientes e combinamos as nossas equipes com as suas necessidades. Se o escopo do projeto mudar, mudamos a configuração.</p>
  <a class="btn">Read More</a>
</section>

<section class="expertise">
  <h2>Expertise</h2>
  <p>Um núcleo de recursos seniores, combinado com especialistas do setor, garante resultados sustentáveis para nossos clientes. Nós adaptamos a equipe e os esforços para cada situação e criamos impacto através de insights e orientação para as pessoas. Quando solicitado, nos juntamos a especialistas e pioneiros de todos os cantos do mundo.</p>

  <div class="panel" style="top:250px">
    <h3>Sectors</h3>
    <span class="arrow l">‹</span><span class="arrow r">›</span>
    <div class="cards">
      <div class="card"><svg viewBox="0 0 24 24"><circle cx="7" cy="15" r="5"/><circle cx="17" cy="15" r="5"/><circle cx="12" cy="7" r="5"/></svg>Bens<br>de Consumo</div>
      <div class="card"><svg viewBox="0 0 24 24"><text x="12" y="21" text-anchor="middle" font-size="24" font-weight="700" font-family="Lato,sans-serif">$</text></svg>Serviços<br>Financeiros</div>
      <div class="card"><svg viewBox="0 0 24 24"><circle cx="14" cy="3.5" r="2.5"/><path d="M12 7l-4 5 3 2-2 8h2l3-7 3 3v5h2v-6l-3-4 1-3 3 2 1-2-5-3z"/></svg>Esportes e Grandes<br>Eventos</div>
      <div class="card"><svg viewBox="0 0 24 24"><rect x="2" y="7" width="12" height="9"/><path d="M15 10h4l3 3v3h-7z"/><circle cx="6" cy="18" r="2"/><circle cx="18" cy="18" r="2"/></svg>Transporte &amp;<br>Logística</div>
      <div class="card"><svg viewBox="0 0 24 24"><path d="M12 2a6 6 0 0 0-4 10.5V16h8v-3.5A6 6 0 0 0 12 2zm0 2a4 4 0 0 1 2.7 7l-.7.6V14h-4v-2.4l-.7-.6A4 4 0 0 1 12 4z"/><rect x="9" y="17" width="6" height="2"/><rect x="10" y="20" width="4" height="2"/></svg>Energia &amp; Meio<br>Ambiente</div>
    </div>
  </div>

  <div class="panel" style="top:565px">
    <h3>Services</h3>
    <span class="arrow l">‹</span><span class="arrow r">›</span>
    <div class="cards">
      <div class="card"><svg viewBox="0 0 24 24"><path d="M5 2h9l5 5v15H5z"/><rect x="8" y="11" width="8" height="1.6" fill="#fff"/><rect x="8" y="15" width="8" height="1.6" fill="#fff"/></svg>Planejamento<br>Estratégico</div>
      <div class="card"><svg viewBox="0 0 24 24"><circle cx="12" cy="7" r="3.5"/><circle cx="5" cy="9" r="2.5"/><circle cx="19" cy="9" r="2.5"/><path d="M6 20c0-4 3-7 6-7s6 3 6 7zM0 19c0-3 2-5 5-5 1 0 2 .3 2.5 1-1.5 1.5-2.3 3-2.5 4zM24 19c0-3-2-5-5-5-1 0-2 .3-2.5 1 1.5 1.5 2.3 3 2.5 4z"/></svg>Pessoas &amp;<br>Organização</div>
      <div class="card"><svg viewBox="0 0 24 24"><rect x="2" y="21" width="20" height="1.5"/><rect x="2" y="3" width="1.5" height="19"/><rect x="6" y="12" width="3" height="8"/><rect x="11" y="7" width="3" height="13"/><rect x="16" y="10" width="3" height="10"/></svg>Data<br>Analytics</div>
      <div class="card"><svg viewBox="0 0 24 24"><path d="M12 4a8 8 0 0 1 7.4 5H22l-3.5 4-3.5-4h2.2A5.8 5.8 0 0 0 6.8 8.4L5 7A8 8 0 0 1 12 4zM4.6 15H2l3.5-4 3.5 4H6.8a5.8 5.8 0 0 0 10.4.6L19 17a8 8 0 0 1-14.4-2z"/></svg>Transformação</div>
      <div class="card"><svg viewBox="0 0 24 24"><path d="M4 5h16v11H4zm2 2v7h12V7z"/><rect x="1" y="17" width="22" height="2"/></svg>Training</div>
    </div>
  </div>
</section>

<section class="cases">
  <h2>Cases</h2>
  <p>A nossa equipe sênior tem ampla experiencia em projetos de alto impacto. Algumas dessas experiências incluem:</p>
  <div class="case-photo" role="img" aria-label="Equipe de negócios analisando documentos sobre uma mesa"></div>
  <ul class="case-list">
    <li><svg viewBox="0 0 18 18"><circle cx="9" cy="9" r="9" fill="#fff"/><path d="M5 9.2l2.7 2.6L13 6.5" stroke="#3176b5" stroke-width="2" fill="none"/></svg>Identificação das principais sinergias, elaboração do modelo de negócios e do plano de integração de duas Grandes Instituições Financeiras Brasileiras; coordenação e acompanhamento da implementação do PMO (Project Management Office).</li>
    <li><svg viewBox="0 0 18 18"><circle cx="9" cy="9" r="9" fill="#fff"/><path d="M5 9.2l2.7 2.6L13 6.5" stroke="#3176b5" stroke-width="2" fill="none"/></svg>Desenvolvimento do orçamento anual e plano de investimento trienal para Grande Empresa Brasileira de Serviços Financeiros, identificando oportunidades de melhoria de 9% do orçamento total.</li>
    <li><svg viewBox="0 0 18 18"><circle cx="9" cy="9" r="9" fill="#fff"/><path d="M5 9.2l2.7 2.6L13 6.5" stroke="#3176b5" stroke-width="2" fill="none"/></svg>Desenvolvimento do orçamento anual e plano de investimento trienal para Grande Empresa Brasileira de Serviços Financeiros, identificando oportunidades de melhoria de 9% do orçamento total.</li>
  </ul>
  <a class="btn light">Read More</a>
</section>

<section class="ecosystem">
  <h2>Ecosistema</h2>
  <p>Nos juntamos a especialistas globais e pioneiros de todo o mundo. A necessidade de velocidade e complexidade de problemas exige uma abordagem flexível, e nosso ecossistema oferece acesso a conhecimento exclusivo de líderes da indústria de classe mundial.</p>
  <div class="partners">
    <div class="partner"><h3>Nexora</h3><p>Rede global com mais de 500 mil experts independentes de variadas indústrias</p></div>
    <div class="partner"><h3>Crowd Lens</h3><p>Rede global de especialistas comportamentais</p></div>
    <div class="partner"><h3>Vetra.AI</h3><p>Plataforma de inteligência artificial e prestador de serviços</p></div>
  </div>
  <div class="dots"><b></b><b></b></div>
</section>

<section class="team">
  <h2>Equipe Sênior</h2>
  <div class="members">
    <div class="member"><div class="portrait" role="img" aria-label="Retrato de João Valtério"></div><h3>João Valtério</h3><p>Lorem ipsum dolor sit amet, consectetur adipiscing elit. Vestibulum diam felis, scelerisque ut quam ut...</p></div>
    <div class="member"><div class="portrait" role="img" aria-label="Retrato de Ramon Valtério"></div><h3>Ramon Valtério</h3><p>Administrador de Empresas pela Universidad del Plata Sur (ARG) e Master em Business Administration...</p></div>
    <div class="member"><div class="portrait" role="img" aria-label="Retrato de Alejandro Valtério"></div><h3>Alejandro Valtério</h3><p>Lorem ipsum dolor sit amet, consectetur adipiscing elit. Vestibulum diam felis, scelerisque ut quam ut...</p></div>
  </div>
</section>

<section class="contact">
  <h2>Contato</h2>
  <div class="lead">Avance com confiança.</div>
  <p class="intro">Contate-nos para mais informações sobre como Cadence Partners pode ajudar você a conseguir maiores resultados, otimizar o desempenho e melhorar o crescimento do seu negócio.</p>
  <p class="intro">Utilize o formulário de contato abaixo ou envie nos um e-mail diretamente a <a>contato@cadence-partners.com.br</a></p>
  <div class="form">
    <div class="field">Nome:</div><div class="field">Organização:</div>
    <div class="field">Telefone:</div><div class="field">E-mail:</div>
    <div class="field msg">Mensagem:</div>
  </div>
  <a class="submit">Submit</a>
  <div class="offices">
    <div class="office"><h3>Rio de Janeiro</h3><p>Av. das Palmeiras, 418 - 11º<br>andar – Praia Azul<br>Rio de Janeiro | 20041-312 | RJ</p></div>
    <div class="office"><h3>São Paulo</h3><p>Av. Jardim Alto, 375 - Torre D, 5º<br>andar – Jardim Sereno<br>São Paulo | 04538-127 | SP</p></div>
    <div class="office"><h3>Buenos Aires</h3><p>Av. Costanera Norte 1870 - Las Acacias<br>Buenos Aires | B1642 KTR<br>Argentina</p></div>
  </div>
</section>

<section class="footer">
  <ul><li>Princípios</li><li>Expertise</li><li>Cases</li><li>Ecosistema</li><li>Equipe Sênior</li><li>Contato</li></ul>
  <small>Copyright © 2019. Company Name. All Right reserved</small>
  <div class="social"><i></i><i></i><i></i><i></i><i></i></div>
</section>

</body>
</html>
```